Snoutsaver.net Dog Coupon Site Website Design

TailThrift - Dog Coupon Site Design Brief

Project Overview
**Site Name:** SnoutSaver.net
**Purpose:** A modern coupon aggregation platform specifically for dog and pet-related products and services
**Target Audience:** Dog owners, pet enthusiasts, budget-conscious pet parents

Brand Identity & Visual Direction

Typography
- **Headers:** Modern sans-serif (Inter or similar) - Clean and friendly
- **Body:** Readable sans-serif with good mobile legibility
- **Accent:** Playful but professional font for coupon codes

Design Principles
- **Flat Design:** Clean, minimal with subtle shadows
- **Friendly & Approachable:** Rounded corners, soft edges
- **Trust-Building:** Clear pricing, transparent savings
- **Scannable:** Easy-to-read coupon codes and offers

## User Experience & Functionality

### Homepage Features
1. **Hero Section**
- Clear value proposition
- Search functionality
- Featured savings highlight

2. **Coupon Cards**
- One-click copy functionality
- Clear discount display
- Store/brand logos
- Expiration dates
- "Get Deal" call-to-action

3. **Navigation**
- Categories (Food, Toys, Health, Services, etc.)
- Popular stores
- Latest deals

### Interactive Elements
- **Copy Button:** Instant feedback when coupon copied
- **Deal Pages:** Detailed offer information, terms, store details
- **Search & Filter:** By category, store, discount amount
- **Mobile Menu:** Hamburger navigation for mobile

## Technical Requirements

### Responsive Design
- **Mobile-First:** Optimized for touch interactions
- **Tablet:** Adapted layout for medium screens
- **Desktop:** Full-width utilization with sidebar potential

### Performance
- **Fast Loading:** Optimized images, minimal JavaScript
- **Accessibility:** WCAG compliant, screen reader friendly
- **SEO Optimized:** Structured data for deals and offers

## Content Strategy

### Deal Categories
- Dog Food & Treats
- Toys & Accessories
- Health & Grooming
- Training & Services
- Outdoor & Travel

### Key Messaging
- "Save on everything your dog loves"
- "Verified deals updated daily"
- "Your pup deserves the best for less"

## Conversion Optimization

### Trust Elements
- Deal verification badges
- User reviews/ratings
- Clear savings calculations
- Expiration date transparency

### Call-to-Actions
- "Copy Code" (primary action)
- "Get Deal" (secondary action)
- "View All [Store] Deals"

## Success Metrics
- Coupon copy rate
- Click-through to retailer
- User return visits
- Mobile vs desktop usage
- Category performance

This design brief ensures a user-friendly, trustworthy platform that makes finding and using pet deals effortless while maintaining a warm, dog-loving community feel.

1. Design Objective
Create a warm, energetic space where dog lovers instantly feel welcomed and confident they’re finding genuine savings for their furry friends. Everything from the layout to the smallest icon should reinforce trust, delight, and simplicity.
2. Visual Personality
Color Palette: Soft, cheerful hues—think warm yellows and gentle blues—that evoke sunshine and playfulness without overwhelming.
Typography:
Headings: A modern, friendly sans‑serif (like Inter) with open letterforms to feel approachable.
Body Copy: Highly legible sans‑serif with generous line spacing for comfort on small screens.
Accent Font: A slightly quirky, hand‑drawn style used sparingly for coupon codes and special call‑outs, giving a personal, “paw‑picked” touch.
Imagery & Icons: Real‑life photographs of happy dogs interspersed with clean line‑icons of bones, paw prints, and hearts. Rounded shapes and subtle shadows keep the look soft and contemporary.
3. Layout & Hierarchy
Hero Area:
Full‑bleed image of a joyful dog, overlaid with a single, punchy tagline (“Save on everything your dog loves”).
Prominent search bar centered to invite exploration.
Offer Grid:
Generous white space around each coupon card so the eye can rest and scan easily.
Coupon cards feature a bold discount label, brand logo, and a friendly “Get Deal” button.
A playful “Copied!” animation briefly replaces the button once the code is grabbed.
Navigation:
A fixed header with clear category labels (Food, Toys, Health, Services).
A secondary “Popular Stores” carousel below to spotlight key partners.
4. Interaction & Motion
Micro‑interactions:
Hover state for cards subtly lifts the card and deepens its shadow, inviting a click.
Copy‑code button pulses once on hover, hinting at its one‑click magic.
Transitions:
Smooth fades between deal filters and search results to reassure users that the site is responding.
Loading indicators shaped like spinning collars or wagging tails to keep the theme consistent.
5. Accessibility & Inclusivity
Ensure all text meets contrast standards so every pet parent—regardless of vision—can read offers with ease.
Interactive elements sized for easy tapping on touchscreens.
Alt‑text for all imagery describing dogs, products, and actions for screen‑reader users.
6. Emotional Tone
From the moment someone lands on SnoutSaver.net, they should feel the joy of treating their dog without guilt. Friendly copy (“Your pup deserves the best for less”) paired with bright visuals will create a sense of community and shared passion.
7. Success by Design
Scan‑ability: Users should spot great deals in under two seconds.
Trust Signals: Badges (“Verified Savings”), clear expiration dates, and reviewer star icons should feel earned and prominent.
Return Visits: A “My Favorite Deals” heart icon encourages saving and returning, reinforced by subtle reminders in the UI.
This design approach keeps dog lovers front and center—making sure every graphic, font choice, and interaction feels like it was lovingly tailored for them.

Target Market(s)

Dog Lovers looking for good deals

Industry/Entity Type

Coupon Code

Number of Pages Required

4 page

Font styles to use
Sans Serif

Requirements
Must have
• Modern look, coupon copy cards it's a deal site and I want the coupon code and copy in the coupon card, blog section, review section, modern footer/header
Nice to have
• Modern coupon code website, easy to use

```html
<!DOCTYPE html>
<html lang="en">
<head>
<meta charset="utf-8">
<title>Snout Saver – Save on everything your dog loves</title>
<link href="https://fonts.googleapis.com/css2?family=Inter:wght@300;400;500;600;700;800&family=Poppins:wght@400;500;600&display=swap" rel="stylesheet">
<style>
:root{
  --yellow:#fdd928;
  --yellow-soft:#fdfbe3;
  --blue:#2f5be8;
  --blue-soft:#aec3f5;
  --ink:#161616;
  --muted:#6f6f6f;
  --line:#d9d9d9;
  --hero:#f1f1ef;
  --footer:#191919;
  --pink:#f6c9cc;
  --red:#d8282e;
}
*{box-sizing:border-box;margin:0;padding:0}
html,body{width:1200px;height:4518px;overflow:hidden}
body{font-family:"Inter",sans-serif;color:var(--ink);background:#fff;position:relative}
.abs{position:absolute}
.btn{position:absolute;display:flex;align-items:center;justify-content:center;border-radius:30px;font-weight:700;font-size:15px;background:var(--yellow);color:var(--ink);z-index:2}
.ph{position:absolute}

/* header */
.site-header{position:absolute;left:0;top:0;width:1200px;height:80px;z-index:3}
.brand{position:absolute;left:108px;top:20px;display:flex;align-items:center;gap:10px}
.brand-dot{width:36px;height:36px;border-radius:50%;background:var(--blue);display:block;flex:none}
.brand-name{font-size:28px;font-weight:500;letter-spacing:.5px;color:var(--ink);white-space:nowrap}
.nav-tab{position:absolute;left:358px;top:0;width:510px;height:52px;background:#fff;border-radius:0 0 28px 28px}
.nav{position:absolute;left:388px;top:15px;display:flex;gap:44px;font-size:16px}
.nav a{color:var(--ink);text-decoration:none}
.nav a.active{color:var(--blue);font-weight:500;border-bottom:2px solid var(--blue);padding-bottom:2px}
.contact-btn{left:955px;top:18px;width:134px;height:40px;font-size:15px}

/* hero */
.hero-bg{position:absolute;left:0;top:0;width:1200px;height:660px}
.hero-art{left:690px;top:40px;width:510px;height:560px;border-radius:50% 0 0 50%;background:radial-gradient(ellipse at 45% 40%,#6a6a6a 0,#9a9a9a 25%,#dcdcd8 48%,rgba(241,241,239,0) 70%);z-index:0}
.hero-title{position:absolute;left:90px;top:142px;width:600px;text-align:center;font-size:44px;font-weight:400;line-height:1.2;letter-spacing:.5px;z-index:2}
.hero-title b{color:var(--yellow);font-weight:800}
.hero-sub{position:absolute;left:140px;top:270px;width:500px;text-align:center;font-size:14px;line-height:1.85;z-index:2}
.search{position:absolute;left:110px;top:350px;width:560px;height:56px;background:#fff;border-radius:30px;box-shadow:0 4px 18px rgba(0,0,0,.07);display:flex;align-items:center;padding-left:26px;font-size:13px;color:#b3b3b3;z-index:2}
.search-go{position:absolute;right:6px;top:8px;width:40px;height:40px;border-radius:50%;background:var(--yellow);display:flex;align-items:center;justify-content:center}

/* coupons */
.coupon{position:absolute;top:805px;width:314px;height:388px;border:1.5px solid var(--line);border-radius:14px;background:#fff}
.coupon .logo{position:absolute;left:26px;top:26px;font-size:36px;font-weight:500;letter-spacing:1px}
.sticker{position:absolute;right:18px;top:20px;width:48px;height:48px;border-radius:50%;background:var(--pink);color:#fff;font-size:8px;font-weight:700;display:flex;align-items:center;justify-content:center;text-align:center;line-height:1.1}
.coupon .fine{position:absolute;left:26px;top:82px;width:262px;font-size:9.5px;line-height:1.9;color:var(--muted);text-align:center}
.coupon .next{position:absolute;left:0;top:170px;width:100%;font-size:11px;font-weight:600;text-align:center}
.coupon .rule{position:absolute;left:22px;top:203px;width:270px;border-top:1.5px dashed #b8b8b8}
.coupon .expiry{position:absolute;left:0;top:222px;width:100%;text-align:center;font-size:10.5px;font-weight:500}
.coupon .label{position:absolute;left:0;top:246px;width:100%;text-align:center;font-size:22px;font-weight:700;letter-spacing:1.5px}
.coupon .code{position:absolute;left:0;top:284px;width:100%;text-align:center;font-size:18px;font-weight:700;color:var(--blue)}
.coupon .deal-btn{left:100px;top:322px;width:110px;height:38px;background:var(--blue-soft);font-size:13px}

.feature{position:absolute;left:410px;top:760px;width:362px;height:480px;background:var(--yellow);border-radius:14px}
.feature-brand{position:absolute;left:28px;top:28px;display:flex;align-items:center;gap:10px}
.feature-brand .brand-dot{width:40px;height:40px}
.feature-brand span{font-size:28px;font-weight:500}
.stars{color:var(--ink);font-size:12px;letter-spacing:2px}
.feature .fine{position:absolute;left:20px;top:113px;width:322px;text-align:center;font-size:10px}
.feature .off{position:absolute;left:0;top:140px;width:362px;text-align:center;font-size:34px;font-weight:700;padding-right:40px}
.special{position:absolute;left:288px;top:148px;width:50px;height:50px;border-radius:50%;background:var(--red);color:#fff;font-size:8px;font-weight:700;display:flex;align-items:center;justify-content:center;text-align:center;line-height:1.1}
.feature .next{position:absolute;left:0;top:198px;width:362px;text-align:center;font-size:12px;font-weight:600}
.corner{position:absolute;right:0;top:0;width:70px;height:56px}
.ticket-txt{position:absolute;left:28px;top:240px;width:306px;text-align:center}
.ticket-txt .expiry{margin-top:46px;font-size:11px;font-weight:500}
.ticket-txt .label{margin-top:12px;font-size:25px;font-weight:700;letter-spacing:1.5px}
.ticket-txt .code{margin-top:4px;font-size:20px;font-weight:600;color:var(--yellow);letter-spacing:1px}
.copy-btn{left:83px;top:145px;width:140px;height:44px;background:var(--blue);color:#fff;font-size:16px;font-weight:500}

/* titles */
.sec-title{position:absolute;left:0;width:1200px;display:flex;justify-content:center;align-items:center;gap:12px;font-size:42px;font-weight:400}
.sec-title b{font-weight:800}
.sec-title .brand-dot{width:30px;height:30px}

/* categories */
.cat{position:absolute;top:1537px;width:150px;text-align:center}
.cat-tile{position:relative;width:142px;height:142px;margin:0 auto}
.cat-tile .shadow{position:absolute;left:8px;top:8px;width:134px;height:134px;border-radius:24px}
.cat-tile .face{position:absolute;left:0;top:0;width:134px;height:134px;border-radius:24px;background:#fff;border:1.5px dashed #777;overflow:hidden}
.cat-tile .face .ph{left:14px;top:14px;width:106px;height:106px;border-radius:16px}
.cat-name{margin-top:30px;font-size:16px;font-weight:500;white-space:nowrap}

/* about */
.about-text{position:absolute;left:160px;top:1900px;width:880px;text-align:center;font-size:14px;line-height:1.95}
.about-text p+p{margin-top:24px}

/* store */
.store-card{position:absolute;top:2882px;width:300px;height:354px;border:1.5px solid var(--line);border-radius:14px;background:#fff}
.store-card .ph{left:12px;top:12px;width:276px;height:274px;border-radius:10px}
.store-card .name{position:absolute;left:0;top:304px;width:100%;text-align:center;font-size:22px;font-weight:500}
.arrow-btn{position:absolute;top:3039px;width:38px;height:38px;border-radius:50%;border:1.5px solid #777;display:flex;align-items:center;justify-content:center}

/* reviews */
.review{position:absolute;width:312px;height:340px;background:#fff;border:1.5px solid var(--line);padding:36px 16px 0 16px;font-family:"Poppins",sans-serif}
.review.raised{border:none;box-shadow:0 6px 26px rgba(0,0,0,.1)}
.review .rstars{color:#f6b21b;font-size:18px;letter-spacing:1px}
.review p{margin-top:16px;font-size:15.5px;line-height:1.75;color:#222}
.reviewer{display:flex;align-items:center;gap:12px;margin-top:18px}
.avatar{width:64px;height:64px;border-radius:50%;background:linear-gradient(135deg,#d8c2ad,#8f7a69);display:block}
.reviewer b{display:block;font-family:"Inter",sans-serif;font-size:15px}
.reviewer span{font-size:13px;color:#9a9a9a}
.g-dot{position:absolute;right:14px;top:22px;width:30px;height:30px;border-radius:50%;border:4px solid #4c84f0}

/* footer */
.footer{position:absolute;left:0;top:4115px;width:1200px;height:403px;background:var(--footer);color:#fff}
.footer .brand{left:110px;top:65px}
.footer .brand-dot{width:58px;height:58px}
.footer .brand-name{color:#fff;font-size:36px}
.badge-round{position:absolute;left:112px;top:180px;width:78px;height:78px;border-radius:50%;background:linear-gradient(135deg,#e8b23a,#a6301f)}
.badge-rect{position:absolute;left:212px;top:196px;width:118px;height:46px;border-radius:6px;background:#3a8f3a}
.fcol{position:absolute;top:80px}
.fcol h4{font-size:20px;font-weight:500;margin-bottom:20px}
.fcol li{list-style:none;font-size:14px;margin-bottom:17px;display:flex;align-items:center;gap:10px}
.fcol li::before{content:"→";color:#bbb;font-size:13px}
.fcontact{position:absolute;left:915px;top:80px}
.fcontact h4{font-size:20px;font-weight:500;margin-bottom:22px}
.crow{display:flex;gap:14px;align-items:flex-start;font-size:14px;margin-bottom:22px;line-height:1.8}
.cicon{width:32px;height:32px;border-radius:50%;background:#fff;flex:none;display:flex;align-items:center;justify-content:center}
.fbar{position:absolute;left:110px;top:340px;width:978px;border-top:1px solid #8a8a8a}
.socials{position:absolute;left:110px;top:360px;display:flex;gap:26px}
.socials i{width:32px;height:32px;border-radius:50%;background:#fff;display:block}
.copyright{position:absolute;right:112px;top:366px;font-size:15px;font-weight:500}
</style>
</head>
<body>

<svg class="hero-bg" viewBox="0 0 1200 660" aria-hidden="true">
  <path d="M0 0H1200V560C1080 600 980 640 820 625C650 610 560 560 380 580C240 595 120 640 0 620Z" fill="var(--hero)"/>
</svg>

<header class="site-header">
  <div class="brand"><i class="brand-dot"></i><span class="brand-name">SNOUT SAVER</span></div>
  <div class="nav-tab"></div>
  <nav class="nav">
    <a class="active" href="#">Home</a>
    <a href="#">Categories ⌄</a>
    <a href="#">Popular stores</a>
    <a href="#">Latest deals</a>
  </nav>
  <a class="btn contact-btn">CONTACT US</a>
</header>

<section class="hero">
  <div class="ph hero-art" role="img" aria-label="Happy French bulldog surrounded by colourful dog toys"></div>
  <h1 class="hero-title">SAVE ON EVERYTHING<br>YOUR <b>DOG LOVES</b></h1>
  <p class="hero-sub">We're a dog-loving community dedicated to helping pet parents save on the best for their furry friends.</p>
  <div class="search">Category &nbsp;|&nbsp; Discount &nbsp;|&nbsp; Coupon Code &nbsp;|&nbsp; Search......
    <span class="search-go"><svg width="14" height="14" viewBox="0 0 14 14"><circle cx="6" cy="6" r="4.2" fill="none" stroke="#161616" stroke-width="2"/><path d="M9 9l3.5 3.5" stroke="#161616" stroke-width="2"/></svg></span>
  </div>
  <a class="btn" style="left:320px;top:440px;width:138px;height:48px">GET DEAL</a>
  <div class="ph" role="img" aria-label="Yellow bone toy" style="left:160px;top:605px;width:118px;height:60px;border-radius:30px;background:var(--yellow)"></div>
</section>

<section class="coupons">
  <article class="coupon" style="left:53px">
    <div class="logo">Nibblo</div>
    <span class="sticker">SHOP<br>NOW</span>
    <p class="fine">Save on premium kibble and crunchy treats when you shop online this week with our verified code.</p>
    <p class="next">on your next purchase</p>
    <div class="rule"></div>
    <p class="expiry">Expiry dates: 10 June 2025</p>
    <p class="label">COUPON CODE</p>
    <p class="code">CS45SALE</p>
    <a class="btn deal-btn">Get Deal</a>
  </article>

  <article class="feature">
    <div class="feature-brand"><i class="brand-dot"></i><div><span>SNOUTSAVER</span><div class="stars">★★★★★</div></div></div>
    <svg class="corner" viewBox="0 0 70 56"><path d="M36 30L50 16M40 16H50V26" stroke="#161616" stroke-width="2" fill="none"/></svg>
    <p class="fine">Save on chews, beds and walk gear at partner stores.</p>
    <p class="off">15% OFF</p>
    <span class="special">SPECIAL<br>OFFER</span>
    <p class="next">on your next purchase</p>
    <svg class="abs" style="left:-10px;top:230px" width="382" height="240" viewBox="0 0 382 240" aria-hidden="true">
      <circle cx="10" cy="14" r="14" fill="#fff"/><circle cx="372" cy="14" r="14" fill="#fff"/>
      <path d="M36 14H346" stroke="#fff" stroke-width="3" stroke-dasharray="10 8"/>
      <path d="M38 30H344V218l-12 10-12-10-12 10-12-10-12 10-12-10-12 10-12-10-12 10-12-10-12 10-12-10-12 10-12-10-12 10-12-10-12 10-12-10-12 10-12-10-12 10-12-10-12 10-12-10-12 10-12-10-12 10-12-10-12 10-12-10-12 10-12-10Z" fill="#fff"/>
    </svg>
    <div class="ticket-txt">
      <p class="expiry">Expiry dates: 12 June 2025</p>
      <p class="label">COUPON CODE</p>
      <p class="code">BS45SALE</p>
      <a class="btn copy-btn">COPY CODE</a>
    </div>
  </article>

  <article class="coupon" style="left:812px">
    <div class="logo">Furvana</div>
    <span class="sticker">SHOP<br>NOW</span>
    <p class="fine">Save on premium kibble and crunchy treats when you shop online this week with our verified code.</p>
    <p class="next">on your next purchase</p>
    <div class="rule"></div>
    <p class="expiry">Expiry dates: 10 June 2025</p>
    <p class="label">COUPON CODE</p>
    <p class="code">CS45SALE</p>
    <a class="btn deal-btn">Copied</a>
  </article>

  <a class="btn" style="left:530px;top:1307px;width:140px;height:48px">VIEW ALL</a>
</section>

<section class="categories">
  <h2 class="sec-title" style="top:1445px"><i class="brand-dot"></i><span>OUR <b>CATEGORIES</b></span></h2>
  <div class="cat" style="left:108px"><div class="cat-tile"><i class="shadow" style="background:#5bd44f"></i><div class="face"><div class="ph" role="img" aria-label="Bowl of dog kibble" style="background:linear-gradient(135deg,#e6d3a8,#b07a3a)"></div></div></div><p class="cat-name">Dog Food &amp; Treats</p></div>
  <div class="cat" style="left:315px"><div class="cat-tile"><i class="shadow" style="background:#8fe3dc"></i><div class="face"><div class="ph" role="img" aria-label="Corgi playing with a toy" style="background:linear-gradient(135deg,#f1e4d6,#c98a55)"></div></div></div><p class="cat-name">Toys &amp; Accessories</p></div>
  <div class="cat" style="left:523px"><div class="cat-tile"><i class="shadow" style="background:#c9c9c9"></i><div class="face"><div class="ph" role="img" aria-label="Groomed poodle" style="background:linear-gradient(135deg,#f3e6dc,#c06a3c)"></div></div></div><p class="cat-name">Health &amp; Grooming</p></div>
  <div class="cat" style="left:728px"><div class="cat-tile"><i class="shadow" style="background:var(--yellow)"></i><div class="face"><div class="ph" role="img" aria-label="Border collie lying down" style="background:linear-gradient(135deg,#f0f0f0,#555)"></div></div></div><p class="cat-name">Training &amp; Services</p></div>
  <div class="cat" style="left:938px"><div class="cat-tile"><i class="shadow" style="background:#b5b1f0"></i><div class="face"><div class="ph" role="img" aria-label="Dog relaxing outdoors" style="background:linear-gradient(135deg,#f0ece6,#a89880)"></div></div></div><p class="cat-name">Outdoor &amp; Travel</p></div>
</section>

<section class="about">
  <h2 class="sec-title" style="top:1822px"><i class="brand-dot"></i><span>ABOUT <b>SNOUT SAVER</b></span></h2>
  <div class="about-text">
    <p>At SnoutSaver, we believe every dog deserves top-quality treats, toys, and care—without breaking the bank. That's why we created a place where pet parents can find verified, up-to-date coupons and deals on everything their pup loves.We sniff out the web's best pet discounts—on food, grooming, gear, services, and more—and bring them together in one easy-to-use platform.</p>
    <p>Whether you're a new dog owner or a seasoned pup pro, SnoutSaver makes it effortless to save.We're a team of dog lovers, budget hunters, and savvy savers who saw a gap in the market. Big coupon sites often bury the good stuff under layers of ads or outdated links. We wanted better for our fellow pet parents.That's why every deal on SnoutSaver is hand-checked and clearly labeled with savings, expiration dates, and retailer info. No fluff—just real deals.</p>
  </div>
  <a class="btn" style="left:523px;top:2155px;width:154px;height:46px">READ MORE</a>
  <div class="ph" role="img" aria-label="Row of nine happy dogs of different breeds sitting together" style="left:80px;top:2255px;width:1040px;height:290px;border-radius:120px 120px 10px 10px;background:linear-gradient(90deg,#e9d6c3,#5a4a40 20%,#d7924f 35%,#efe7df 55%,#c97d45 72%,#f3efea 85%,#d9a070)"></div>
</section>

<svg class="abs" style="left:0;top:2590px" width="1200" height="820" viewBox="0 0 1200 820" aria-hidden="true">
  <path d="M0 20C150 0 250 110 420 90C600 70 700 20 860 40C1000 55 1100 90 1200 70V760C1050 810 900 780 700 770C450 760 250 820 0 790Z" fill="var(--yellow-soft)"/>
</svg>
<section class="store">
  <h2 class="sec-title" style="top:2784px"><i class="brand-dot"></i><span>OUR PRODUCT <b>STORE</b></span></h2>
  <span class="arrow-btn" style="left:36px"><svg width="16" height="12"><path d="M15 6H2M6 1L1 6l5 5" stroke="#555" stroke-width="1.5" fill="none"/></svg></span>
  <span class="arrow-btn" style="left:1125px"><svg width="16" height="12"><path d="M1 6H14M10 1l5 5-5 5" stroke="#555" stroke-width="1.5" fill="none"/></svg></span>
  <article class="store-card" style="left:111px"><div class="ph" role="img" aria-label="Dog food bags on a store shelf" style="background:linear-gradient(135deg,#2c4c62,#d2812e 60%,#3c2f28)"></div><p class="name">Food</p></article>
  <article class="store-card" style="left:451px"><div class="ph" role="img" aria-label="Golden retriever with a smiling vet" style="background:linear-gradient(135deg,#f3ece2,#d7a96a 50%,#7cc7c0)"></div><p class="name">Health</p></article>
  <article class="store-card" style="left:791px"><div class="ph" role="img" aria-label="Puppy playing with toys" style="background:linear-gradient(135deg,#4a5a6a,#b9783c 50%,#e2b43b)"></div><p class="name">Toy</p></article>
  <a class="btn" style="left:500px;top:3283px;width:200px;height:48px">VIEW ALL STORE</a>
</section>

<section class="reviews">
  <h2 class="sec-title" style="top:3534px"><i class="brand-dot"></i><span>WHAT OUR <b>CUSTOMER SAYS</b></span></h2>
  <article class="review" style="left:111px;top:3632px">
    <div class="rstars">★★★★★</div>
    <p>Temporibus autem quibusdam et aut officiis debitis aut rerum neus saepe facere mus, onis voluptas eveniet ut et voluptates repudae sint et molestiae non lorem recusadae.</p>
    <div class="reviewer"><i class="avatar"></i><div><b>Owen Haskell</b><span>United States</span></div></div>
  </article>
  <article class="review raised" style="left:452px;top:3672px">
    <i class="g-dot"></i>
    <div class="rstars">★★★★★</div>
    <p>Itaque earum rerum hic tenetur a sapiene delectus, ut aut reiciels volupatibus maiores alias conse uatur aut perferndis doloribus asperiores reiciendis voluptatbus repellat</p>
    <div class="reviewer"><i class="avatar"></i><div><b>Lenora</b><span>United States</span></div></div>
  </article>
  <article class="review" style="left:793px;top:3632px">
    <div class="rstars">★★★★★</div>
    <p>At vero eos et accusamus et iusto odio dignissimos ducimus qui blaiis praesentium volupttum deleniti atque corrupti quos dolores et quas occaecati cupie non provident</p>
    <div class="reviewer"><i class="avatar"></i><div><b>Marcus Pell</b><span>United States</span></div></div>
  </article>
  <article class="review raised" style="left:1140px;top:3672px">
    <div class="rstars">★★★★★</div>
    <p>At vero eos iusto odio qui blaiis deleniti dolores non provident</p>
  </article>
</section>

<footer class="footer">
  <div class="brand"><i class="brand-dot"></i><span class="brand-name">SNOUT SAVER</span></div>
  <i class="badge-round"></i>
  <i class="badge-rect"></i>
  <div class="fcol" style="left:447px"><h4>QUICK LINKS</h4><ul><li>Home</li><li>About</li><li>Categories</li><li>Popular Deals</li><li>Contact Us</li></ul></div>
  <div class="fcol" style="left:680px"><h4>HELP LINKS</h4><ul><li>FAQ</li><li>Terms of use</li><li>Privacy Policy</li><li>Support Links</li><li>Conditions</li></ul></div>
  <div class="fcontact">
    <h4>CONTACT US</h4>
    <div class="crow"><span class="cicon"><svg width="14" height="18" viewBox="0 0 14 18"><path d="M7 1a6 6 0 0 1 6 6c0 4-6 10-6 10S1 11 1 7a6 6 0 0 1 6-6z" fill="#191919"/><circle cx="7" cy="7" r="2.2" fill="#fff"/></svg></span><span>Snout Saver<br>United States</span></div>
    <div class="crow"><span class="cicon"><svg width="16" height="16" viewBox="0 0 16 16"><path d="M3 1l3 3-2 2c1 2 3 4 5 5l2-2 3 3-2 3C7 15 1 9 1 3z" fill="#191919"/></svg></span><span style="line-height:32px">+1 555 010 2040</span></div>
    <div class="crow"><span class="cicon"><svg width="16" height="12" viewBox="0 0 16 12"><rect x="1" y="1" width="14" height="10" rx="1.5" fill="#191919"/><path d="M1 2l7 5 7-5" stroke="#fff" stroke-width="1.3" fill="none"/></svg></span><span style="line-height:32px">hello@snoutsaver.net</span></div>
  </div>
  <div class="fbar"></div>
  <div class="socials"><i></i><i></i><i></i><i></i></div>
  <p class="copyright">Copyrights@2023.Snout Saver.All Rights Reserved</p>
</footer>

</body>
</html>
```